Flat bootstrap design for existing site

I'm looking for a modern flat design based around an existing logo. This has to be a custom design (no external templates), and implemented into a bootstrap framework.

The logo is attached as 2 versions - choose whichever you want, that flows better with whatever design you choose.

Added screenshots of the existing site (currently using the default bootstrap layouts). Please make your designs around those pages in the screenshots (i.e. the homepage only has the postal code input and the header). The active page has 3 screenshots, because I wanted to illustrate the other states that would be visible (in the table rows).

This is a moving/junk removal website, just for some context.

Here's some example websites (flat designs) that I like, just to give you an idea of what I'm after.

https://www.plimvora.com/
https://dacklow.com/
https://trevanu.com/
https://quobrintal.com/en/

Coding

Coded - Design and coding required

Number of Pages Required

5+ page

Colors

Designer to choose colors to be used in the design.

Requirements
Must have
• It must be a modern/simple flat design, that is built around the existing logo (attached).
• It has to be implemented using bootstrap.

```html
<!DOCTYPE html>
<html lang="en">
<head>
<meta charset="utf-8">
<title>Ravelo – Sign In</title>
<link href="https://fonts.googleapis.com/css2?family=Open+Sans:wght@400;600;700&display=swap" rel="stylesheet">
<style>
  :root {
    --brand-sky: #48c8f5;
    --brand-sky-dark: #2eb3e3;
    --text-light: #ffffff;
    --text-muted: #555555;
    --input-text: #666666;
    --footer-bg: #ffffff;
  }
  * { box-sizing: border-box; margin: 0; padding: 0; }
  html, body {
    width: 1200px; height: 614px; overflow: hidden;
    font-family: "Open Sans", Arial, sans-serif;
    background: var(--footer-bg);
  }
  .page { position: relative; width: 1200px; height: 614px; }

  .site-header {
    position: absolute; top: 0; left: 0; width: 1200px; height: 80px;
    background: var(--brand-sky);
  }
  .brand {
    position: absolute; left: 132px; top: 22px;
    display: flex; align-items: center; gap: 8px;
    color: var(--text-light); font-weight: 700; font-size: 28px;
    letter-spacing: 1px; text-decoration: none; line-height: 36px;
  }
  .brand-dot {
    width: 14px; height: 14px; border-radius: 50%;
    background: var(--text-light);
  }
  .main-nav a {
    position: absolute; top: 19px; height: 40px; line-height: 40px;
    color: var(--text-light); text-decoration: none; font-size: 14.4px;
  }
  .nav-book { left: 642px; }
  .nav-how { left: 726px; }
  .nav-driver {
    left: 848px; width: 144px; text-align: center;
    background: var(--brand-sky-dark); border-radius: 3px;
  }
  .nav-signin { left: 1023px; }

  .hero {
    position: absolute; top: 80px; left: 0; width: 1200px; height: 480px;
  }
  .hero-photo {
    position: absolute; inset: 0;
    background:
      radial-gradient(ellipse at 80% 20%, #1f5f7c 0%, rgba(31,95,124,0) 45%),
      radial-gradient(ellipse at 25% 85%, #7a5a20 0%, rgba(122,90,32,0) 40%),
      linear-gradient(135deg, #6f5a44 0%, #8a6f53 40%, #6e5843 70%, #4d4236 100%);
  }
  .hero-shade { position: absolute; inset: 0; background: rgba(0,0,0,0.18); }

  .signin-title {
    position: absolute; top: 115px; left: 0; width: 1200px; text-align: center;
    color: var(--text-light); font-weight: 600; font-size: 39px; line-height: 50px;
    text-shadow: 0 1px 3px rgba(0,0,0,0.35);
  }
  .field {
    position: absolute; left: 448px; width: 304px; height: 48px;
    border: none; background: #fff; padding: 0 22px;
    font-family: inherit; font-size: 13px; color: var(--input-text);
  }
  .field::placeholder { color: var(--input-text); }
  .field-email { top: 181px; }
  .field-password { top: 245px; }
  .btn-login {
    position: absolute; left: 560px; top: 309px; width: 80px; height: 48px;
    border: none; background: var(--brand-sky); color: var(--text-light);
    font-family: inherit; font-weight: 600; font-size: 15px;
  }

  .site-footer {
    position: absolute; top: 560px; left: 0; width: 1200px; height: 54px;
    text-align: center; line-height: 54px;
    font-size: 10.4px; color: var(--text-muted);
  }
</style>
</head>
<body>
<div class="page">
  <header class="site-header">
    <a class="brand" href="#"><span class="brand-dot"></span>RAVELO</a>
    <nav class="main-nav">
      <a class="nav-book" href="#">Book</a>
      <a class="nav-how" href="#">How It Works</a>
      <a class="nav-driver" href="#">Become a Driver</a>
      <a class="nav-signin" href="#">Sign In</a>
    </nav>
  </header>

  <main class="hero">
    <div class="hero-photo" role="img" aria-label="Photo of packed cardboard moving boxes, household items and blue bags"></div>
    <div class="hero-shade"></div>
    <h1 class="signin-title">Please Sign In</h1>
    <form>
      <input class="field field-email" type="email" placeholder="Email Address">
      <input class="field field-password" type="password" placeholder="Password">
      <button class="btn-login" type="submit">LOGIN</button>
    </form>
  </main>

  <footer class="site-footer">Copyright &copy; 2017 Ravelo. All rights reserved.</footer>
</div>
</body>
</html>
```